Coastline Premier Retreats Business Card Design

Design a business card for Coastline Premier Retreats. Look at the website for colors and reference. Card should have logo, name, title, office number, mobile number, email, URL and a tagline like, "Luxury Hotel & Resort Email Marketing" (This might change).

https://www.coastlinepremierretreats.example

The rest I will leave up to your imagination.

Contact Information for Business Card

Logo, name, title, office number, mobile number, email, URL and a tagline like, "Luxury Hotel & Resort Email Marketing" (This might change).

```html
<!DOCTYPE html>
<html lang="en">
<head>
<meta charset="utf-8">
<title>Coastline Premier Retreats – Business Card</title>
<link href="https://fonts.googleapis.com/css2?family=Montserrat:wght@400;500;700&display=swap" rel="stylesheet">
<style>
  :root{
    --backdrop:#adaeae;
    --charcoal:#2b2b2b;
    --steel:#6e6e6e;
    --orange:#f26a1b;
    --paper:#ffffff;
    --ink:#1e1e1e;
    --ghost:#f6f6f6;
  }
  *{margin:0;padding:0;box-sizing:border-box}
  html,body{width:1200px;height:900px;overflow:hidden}
  body{
    background:var(--backdrop);
    font-family:"Montserrat",sans-serif;
    display:flex;flex-direction:column;align-items:center;justify-content:center;gap:40px;
  }
  .card{
    position:relative;width:620px;height:354px;overflow:hidden;
    border-bottom:2px solid var(--orange);
  }
  /* front */
  .card--front{background:var(--charcoal);display:flex;align-items:center;justify-content:center}
  .brand{display:flex;align-items:center;gap:14px}
  .brand__square{width:18px;height:18px;background:var(--orange)}
  .brand__name{
    color:var(--steel);font-weight:700;font-size:28px;letter-spacing:2px;text-transform:uppercase;
  }
  /* back */
  .card--back{background:var(--paper)}
  .ghost-word{
    position:absolute;left:40px;top:40px;
    font-weight:700;font-size:118px;line-height:1;color:var(--ghost);
    letter-spacing:-2px;text-transform:uppercase;white-space:nowrap;
  }
  .identity{
    position:absolute;left:0;top:118px;width:268px;text-align:right;
  }
  .identity__name{color:var(--orange);font-weight:700;font-size:25px}
  .identity__title{color:var(--ink);font-size:13px;margin-top:2px}
  .divider{position:absolute;left:284px;top:100px;width:2px;height:88px;background:var(--orange)}
  .contacts{position:absolute;left:302px;top:102px;list-style:none}
  .contacts li{display:flex;align-items:center;gap:10px;font-size:12.5px;color:var(--ink);height:21px}
  .contacts svg{width:13px;height:13px;fill:var(--orange);flex:none}
  .tagline{
    position:absolute;right:34px;bottom:34px;color:var(--orange);font-weight:700;font-size:14px;
  }
</style>
</head>
<body>
  <section class="card card--front">
    <div class="brand">
      <span class="brand__square"></span>
      <span class="brand__name">Coastline Premier Retreats</span>
    </div>
  </section>

  <section class="card card--back">
    <div class="ghost-word" aria-hidden="true">Coastline</div>
    <div class="identity">
      <div class="identity__name">Rafael Okonte</div>
      <div class="identity__title">Owner</div>
    </div>
    <div class="divider"></div>
    <ul class="contacts">
      <li><svg viewBox="0 0 16 16"><path d="M2 5c0-2 2-3 6-3s6 1 6 3v1h-3V5H5v1H2z M4 7h8l2 6H2z"/></svg>555.201.4470 x 204</li>
      <li><svg viewBox="0 0 16 16"><path d="M4 1h8v14H4z M5.5 2.5v9h5v-9z M7 12.5h2v1H7z" fill-rule="evenodd"/></svg>555.318.2290</li>
      <li><svg viewBox="0 0 16 16"><path d="M1 3h14v10H1z M2 4l6 5 6-5z" fill-rule="evenodd"/></svg>info@coastlinepremierretreats.example</li>
      <li><svg viewBox="0 0 16 16"><circle cx="8" cy="8" r="7"/><path d="M1 8h14M8 1c3 3 3 11 0 14M8 1c-3 3-3 11 0 14" stroke="#fff" stroke-width="1.2" fill="none"/></svg>www.coastlinepremierretreats.example</li>
    </ul>
    <div class="tagline">Luxury Hotel &amp; Resort Email Marketing</div>
  </section>
</body>
</html>
```